Stationery Set for Velmora Company

I need to create full stationery design for my company; Business Cards, Envelops, Letter Heads, Calendar.
In the letter head and Envelops... only contact information and website links.
Our company is a Service Management company with different domains of innovative services including Technology Service Management, Education Services, Outsourcing Management, Events Management.
I need a modern and innovative design specially for the business card. I some transparent designs and I like it, but don't limit your innovation to what I mentioned. Sky is limit for your innovation.

Target Market(s)

Middle East & Africa

Industry/Entity Type

Business Management

Colors
34a7d8
0355a3
85acd3
86cae7
cee9f5
cfdeed
e4daeb
f3f1f8
ecf7fb

Requirements
Must have
• Name, Title, Email, Mobile
Nice to have
• We have multiple locations in USA, KSA, EGY, so I need ideas about how to include all contact details maybe QR / Barcode or something else.
• Please see our locations and contact information: www.brightvelmora.example
Should not have
• Too much text

```html
<!DOCTYPE html>
<html lang="en">
<head>
<meta charset="utf-8">
<title>Velmora Company – Window Envelope</title>
<link rel="stylesheet" href="https://fonts.googleapis.com/css2?family=Quicksand:wght@500;700&family=Cairo:wght@700&display=swap">
<style>
  :root {
    --page: #ffffff;
    --paper: #ffffff;
    --edge: #8a8a8a;
    --brand-blue: #2d63ff;
    --band-light: #dfe8ff;
    --band-mid: #9bb6ff;
    --wave-light: #cfe6f7;
    --wave-deep: #9aa6d4;
    --window-edge: #6f6f6f;
  }
  * { margin: 0; padding: 0; box-sizing: border-box; }
  html, body {
    width: 1200px; height: 1000px; overflow: hidden;
    background: var(--page);
  }
  .canvas { position: relative; width: 1200px; height: 1000px; }
  .envelope {
    position: absolute; left: 25px; top: 92px;
    width: 1150px; height: 816px;
    background: var(--paper);
    border-top: 1px solid var(--edge);
    box-shadow: -6px 6px 10px rgba(0,0,0,0.55);
    overflow: hidden;
  }
  .envelope-art { position: absolute; inset: 0; }
  .brand-name {
    position: absolute; left: 85px; top: 118px;
    font-family: "Quicksand", sans-serif; font-weight: 700;
    font-size: 38px; letter-spacing: 0.5px;
    color: var(--brand-blue);
    display: flex; align-items: center; gap: 12px;
  }
  .brand-dot {
    width: 16px; height: 16px; border-radius: 50%;
    background: var(--brand-blue);
  }
  .brand-arabic {
    position: absolute; left: 86px; top: 214px;
    width: 287px; height: 29px;
    background: var(--brand-blue);
    color: #ffffff;
    font-family: "Cairo", sans-serif; font-weight: 700;
    font-size: 17px; line-height: 29px;
    text-align: center; direction: rtl;
  }
  .sender-address {
    position: absolute; left: 88px; top: 262px;
    font-family: "Quicksand", sans-serif; font-weight: 500;
    font-size: 20px; line-height: 32px;
    color: var(--brand-blue); font-style: normal;
  }
  .address-window {
    position: absolute; left: 642px; top: 561px;
    width: 459px; height: 193px;
    background: var(--paper);
    border: 1px solid var(--window-edge);
    border-radius: 13px;
  }
</style>
</head>
<body>
<div class="canvas">
  <div class="envelope">
    <svg class="envelope-art" width="1150" height="816" viewBox="0 0 1150 816">
      <defs>
        <linearGradient id="waveTone" x1="0" y1="0" x2="0.4" y2="1">
          <stop offset="0" stop-color="var(--wave-light)"/>
          <stop offset="1" stop-color="var(--wave-deep)"/>
        </linearGradient>
        <linearGradient id="bandTone" x1="0" y1="0" x2="1" y2="0">
          <stop offset="0" stop-color="var(--band-light)"/>
          <stop offset="0.34" stop-color="var(--brand-blue)"/>
          <stop offset="0.62" stop-color="var(--band-mid)"/>
          <stop offset="1" stop-color="var(--band-mid)"/>
        </linearGradient>
      </defs>
      <path role="img" aria-label="Soft flowing striped wave decoration"
            d="M0,82 C140,100 280,170 380,140 C450,118 500,95 530,68 C515,160 455,210 380,240 C230,300 80,320 0,415 Z"
            fill="url(#waveTone)" opacity="0.55"/>
      <rect class="footer-band" x="0" y="690" width="1150" height="46" fill="url(#bandTone)"/>
    </svg>

    <div class="brand-name"><span>Velmora Company</span><span class="brand-dot"></span></div>
    <div class="brand-arabic" lang="ar">شركة فيلمورا للخدمات</div>
    <address class="sender-address">
      418 Harbor Crest Lane, 4th<br>
      Floor Marlow Bay CA 90000<br>
      US
    </address>

    <div class="address-window"></div>
  </div>
</div>
</body>
</html>
```